FROSTLINE STUDIO . Whole Body Cryotherapy, Localised Cryotherapy, Cryofacials

Need home page plus services, about, pricing, online booking, contact and blog page

I want something slick, hip and professional. Our studio colours are duck egg blue, white and grey

I would also like a social media scroll at the bottom of every page

I will upload some web designs that I like the look of

Target Market(s)

Men and Women 25-45

Industry/Entity Type

Health And Wellness

Coding

Coded - Design and coding required

Number of Pages Required

5+ page

Font styles to use
Serif
Sans Serif

Requirements
Must have
• Must be eye catching and easy to navigate
Nice to have
• animation
Should not have
• Not sure what the site should not have. I am fairly open to ideas as this is a brand new business.

```html
<!DOCTYPE html>
<html lang="en">
<head>
<meta charset="utf-8">
<title>Frostline Studio – Cryotherapy</title>
<link href="https://fonts.googleapis.com/css2?family=Cinzel:wght@400&family=Montserrat:wght@500;600;700&family=Lato:wght@400;700&family=Great+Vibes&display=swap" rel="stylesheet">
<style>
:root{
  --sage:#8e9e92;
  --sage-dark:#7d8e81;
  --duck:#b7cfc6;
  --duck-light:#c7dbd4;
  --charcoal:#3c443f;
  --ink:#2b2b2b;
  --text:#666;
  --muted:#999;
  --line:#d6dcd8;
  --mist:#f3f5f4;
  --white:#fff;
}
*{margin:0;padding:0;box-sizing:border-box}
html,body{width:1200px;height:4229px;overflow:hidden}
body{position:relative;background:var(--white);font-family:'Lato',sans-serif;color:var(--text)}
.abs{position:absolute}
.photo{position:absolute}
.script{font-family:'Great Vibes',cursive;color:var(--duck);font-size:32px;text-align:center}
.heading{font-family:'Montserrat',sans-serif;font-weight:600;color:var(--sage);font-size:37px;text-align:center;letter-spacing:.5px}
.divider{position:absolute;left:50%;transform:translateX(-50%);width:200px;height:10px}
.divider::before,.divider::after{content:"";position:absolute;top:4px;width:82px;height:1px;background:var(--line)}
.divider::before{left:0}.divider::after{right:0}
.divider span{position:absolute;left:95px;top:0;width:10px;height:10px;border-radius:50%;background:#c9cfcb}
.btn{position:absolute;display:flex;align-items:center;justify-content:center;font-family:'Lato',sans-serif;font-weight:700;font-size:15px;color:var(--white);text-transform:uppercase;background:var(--sage)}

/* top bar */
.topbar{left:0;top:0;width:1200px;height:51px;background:var(--sage)}
.social{display:flex;gap:10px}
.social i{display:block;width:30px;height:30px;border-radius:50%;background:var(--white)}
.topbar .social{position:absolute;left:78px;top:11px}
.contact{position:absolute;top:16px;font-size:15px;color:var(--white);display:flex;align-items:center;gap:12px}

/* nav */
.nav{left:0;top:51px;width:1200px;height:105px;border-bottom:1px solid #eee}
.logo{position:absolute;font-family:'Cinzel',serif;color:var(--sage);text-align:center;line-height:1.2}
.nav .logo{left:80px;top:20px;font-size:28px;width:230px}
.menu{position:absolute;left:418px;top:42px;display:flex;gap:37px;font-size:16px;color:#888}
.menu .active{color:var(--duck)}

/* hero */
.hero{left:0;top:156px;width:1200px;height:573px;background:linear-gradient(100deg,#d9d9d9 0%,#c4c4c4 45%,#9fa3a6 70%,#d6d0d4 100%)}
.hero h1{position:absolute;left:79px;top:130px;font-family:'Montserrat',sans-serif;font-weight:700;font-size:58px;line-height:1.08;color:var(--ink)}
.hero p{position:absolute;left:79px;top:278px;width:430px;font-size:16px;line-height:1.7;color:#333}

/* offers */
.offer{position:absolute;top:924px;width:336px;height:337px;background:var(--white);border:1px solid #e3e3e3;box-shadow:0 2px 6px rgba(0,0,0,.08)}
.offer .photo{left:6px;top:6px;width:322px;height:323px}
.offer-label{position:absolute;top:1166px;width:282px;height:116px;background:var(--white);text-align:center}
.offer-label .script{font-size:26px;color:var(--sage);padding-top:20px;word-spacing:3px}
.offer-label .script.light{color:var(--duck)}
.offer-label h3{font-family:'Montserrat',sans-serif;font-weight:500;font-size:18px;color:var(--ink);margin-top:2px}

/* services */
.tile{position:absolute;width:300px;height:250px;background:var(--mist);text-align:center;border:1px solid #eceeed}
.tile svg{margin-top:28px}
.tile h4{font-family:'Montserrat',sans-serif;font-weight:500;font-size:17px;color:var(--ink);margin-top:14px}
.tile p{font-size:14px;line-height:1.85;color:var(--muted);margin:18px auto 0;width:230px}

/* booking */
.booking h2{position:absolute;left:79px;top:2006px;font-family:'Montserrat',sans-serif;font-weight:600;font-size:36px;color:var(--sage)}
.booking p{position:absolute;left:79px;top:2068px;width:370px;font-size:14px;line-height:1.85;color:var(--muted)}

/* blog */
.blog-bg{left:0;top:2384px;width:1200px;height:604px;background:var(--mist)}
.post{position:absolute;top:2583px;width:241px;height:333px;background:var(--white);box-shadow:0 2px 8px rgba(0,0,0,.07)}
.post .photo{left:21px;top:21px;width:199px;height:187px}
.post p{position:absolute;left:23px;top:229px;width:200px;font-size:15px;line-height:1.6;color:var(--sage)}
.post time{position:absolute;left:23px;top:289px;font-size:15px;color:#555}

/* pricing */
.pricing{left:727px;top:2988px;width:396px;height:470px;background:var(--sage)}
.pricing h2{font-family:'Montserrat',sans-serif;font-weight:600;font-size:36px;color:var(--white);text-align:center;margin-top:62px}
.price-row{position:absolute;left:33px;width:330px;display:flex;justify-content:space-between;align-items:center;color:var(--white);padding-bottom:17px;border-bottom:1px solid rgba(255,255,255,.35)}
.price-row.last{border-bottom:none}
.price-row em{font-family:'Great Vibes',cursive;font-style:normal;font-size:22px;word-spacing:3px}
.price-row b{font-family:'Lato',sans-serif;font-weight:700;font-size:18px}
.outline-btn{position:absolute;left:135px;top:355px;width:126px;height:51px;border:1px solid rgba(255,255,255,.8);color:var(--white);font-weight:700;font-size:15px;display:flex;align-items:center;justify-content:center}

/* newsletter */
.newsletter p{position:absolute;left:320px;top:3644px;width:560px;text-align:center;font-size:15px;line-height:1.75;color:var(--muted)}
.field{position:absolute;top:3729px;width:219px;height:63px;border:1px solid #ccc;display:flex;align-items:center;gap:12px;padding-left:14px;font-size:14px;font-weight:700;color:#888}

/* footer */
.footer{left:0;top:3854px;width:1200px;height:303px;background:var(--duck)}
.footer .logo{left:0;width:1200px;top:67px;font-size:30px;color:var(--white)}
.footer-menu{position:absolute;left:0;width:1200px;top:160px;text-align:center;font-size:15px;color:var(--white)}
.footer-menu span{margin:0 9px}
.footer .social{position:absolute;left:498px;top:206px;gap:8px}
.footer .social i{width:46px;height:46px}
.footer .social i.first{background:var(--sage)}
.copyright{left:0;top:4157px;width:1200px;height:72px;background:var(--sage);color:var(--white);font-size:14px;display:flex;align-items:center;justify-content:center}
</style>
</head>
<body>

<header class="abs topbar">
  <div class="social" aria-label="Social links"><i></i><i></i><i></i><i></i></div>
  <div class="contact" style="left:692px">
    <svg width="18" height="18" viewBox="0 0 24 24" fill="none" stroke="#fff" stroke-width="2"><path d="M5 3h4l2 5-3 2a11 11 0 0 0 6 6l2-3 5 2v4a2 2 0 0 1-2 2A17 17 0 0 1 3 5a2 2 0 0 1 2-2z"/></svg>
    555.014.2290
  </div>
  <div class="contact" style="left:864px">
    <svg width="20" height="15" viewBox="0 0 20 15" fill="none" stroke="#fff" stroke-width="1.6"><rect x="1" y="1" width="18" height="13"/><path d="M1 1l9 7 9-7"/></svg>
    hello@frostlinestudio.com
  </div>
</header>

<nav class="abs nav">
  <div class="logo">FROSTLINE<br>STUDIO</div>
  <div class="menu">
    <span class="active">Home</span><span>About</span><span>Services</span><span>Pricing</span><span>Online Booking</span><span>Blog</span><span>Contact</span>
  </div>
  <svg class="abs" style="left:1102px;top:42px" width="22" height="22" viewBox="0 0 22 22" fill="none" stroke="#333" stroke-width="2"><circle cx="9" cy="9" r="7"/><path d="M14 14l6 6"/></svg>
</nav>

<section class="abs hero" role="img" aria-label="Woman relaxing in a whole body cryotherapy chamber with cold mist">
  <h1>FROSTLINE<br>STUDIO</h1>
  <p>Lorem ipsum dolor sit amet, consectetur adipiscing elit, sed do eiusmod tempor incididunt ut labore et dolore magna aliqua.</p>
  <div class="btn" style="left:77px;top:386px;width:146px;height:52px">Contact Us</div>
  <div class="btn" style="left:238px;top:386px;width:147px;height:52px;background:var(--charcoal)">Read More</div>
</section>

<section class="welcome">
  <div class="abs script" style="left:0;top:784px;width:1200px">Welcome to</div>
  <div class="abs heading" style="left:0;top:820px;width:1200px">FROSTLINE STUDIO</div>
  <div class="divider" style="top:874px"><span></span></div>

  <div class="offer" style="left:76px"><div class="photo" role="img" aria-label="Therapist applying localised cryotherapy to a client's leg" style="background:linear-gradient(135deg,#6f6d6a,#c9c2bd 55%,#e9e4e1)"></div></div>
  <div class="offer" style="left:432px"><div class="photo" role="img" aria-label="Gloved hand holding a cryo applicator over a leg" style="background:linear-gradient(135deg,#5d6a72,#b9c3c9 50%,#e3d6cc)"></div></div>
  <div class="offer" style="left:788px"><div class="photo" role="img" aria-label="Therapist treating a man's back on a treatment table" style="background:linear-gradient(135deg,#e8ecef,#c6ced6 45%,#3a6bb8 80%)"></div></div>

  <div class="offer-label" style="left:103px"><div class="script">Deal Of Week</div><h3>SPECIAL OFFERS</h3></div>
  <div class="offer-label" style="left:459px"><div class="script light">Special Gifts</div><h3>GIFT CARD AVAILABLE</h3></div>
  <div class="offer-label" style="left:815px"><div class="script">Book Now</div><h3>ONLINE APPOINTMENT</h3></div>

  <div class="btn" style="left:103px;top:1282px;width:282px;height:51px">Read More</div>
  <div class="btn" style="left:459px;top:1282px;width:282px;height:51px;background:var(--duck-light)">Read More</div>
  <div class="btn" style="left:815px;top:1282px;width:282px;height:51px">Read More</div>
</section>

<section class="services">
  <div class="photo" role="img" aria-label="Cryofacial treatment with a roller device on a woman's cheek" style="left:0;top:1396px;width:600px;height:500px;background:linear-gradient(120deg,#c7c4c2,#e8dcd4 45%,#d8c0b2 70%,#efeae7)"></div>

  <div class="tile" style="left:600px;top:1396px">
    <svg width="44" height="76" viewBox="0 0 44 76" fill="none" stroke="#888" stroke-width="1.6"><path d="M8 4l6 2c2 8 14 8 16 0l6-2v20l-4 14 6 26-14 8-14-4-6-8 4-22L8 24z"/><path d="M14 40c6 4 12 4 18 0"/></svg>
    <h4>Whole Body Cryotherapy</h4>
    <p>Lorem ipsum dolor sit consectetur elit, sed do eiusmod tempor.</p>
  </div>
  <div class="tile" style="left:900px;top:1396px">
    <svg width="56" height="76" viewBox="0 0 56 76" fill="none" stroke="#888" stroke-width="1.6"><rect x="10" y="24" width="36" height="48" rx="2"/><path d="M10 32h36M18 42h6M30 50h8M16 58h10"/><path d="M28 4v8M18 8l3 6M38 8l-3 6M8 16l5 4M48 16l-5 4"/><circle cx="28" cy="16" r="2"/></svg>
    <h4>Localised Cryotherapy</h4>
    <p>Lorem ipsum dolor sit consectetur elit, sed do eiusmod tempor.</p>
  </div>
  <div class="tile" style="left:600px;top:1646px">
    <svg width="48" height="76" viewBox="0 0 48 76" fill="none" stroke="#888" stroke-width="1.6"><path d="M10 30c0-14 28-14 28 0v14c0 8-6 14-14 14S10 52 10 44z"/><path d="M12 24c6-4 18-4 24 0"/><path d="M4 74c2-10 8-14 20-14s18 4 20 14z"/></svg>
    <h4>Cryofacials</h4>
    <p>Lorem ipsum dolor sit consectetur elit, sed do eiusmod tempor.</p>
  </div>
  <div class="photo" role="img" aria-label="Woman inside a blue-lit cryotherapy chamber" style="left:900px;top:1646px;width:300px;height:250px;background:linear-gradient(160deg,#2d4fd0,#7fa0e6 45%,#d6dde8 75%,#f2f4f7)"></div>
</section>

<section class="booking">
  <h2>ONLINE BOOKING</h2>
  <p>Lorem ipsum dolor sit amet, consectetur adipiscing elit, sed do eiusmod tempor incididunt ut labore et dolore magna aliqua. Ut enim ad minim veniam, quis nostrud exercitation ullamco laboris nisi ut aliquip ex ea there commodo consequat.</p>
  <div class="btn" style="left:77px;top:2220px;width:125px;height:51px">Book Now</div>
  <div class="abs" style="left:655px;top:1959px;width:470px;height:363px;background:var(--duck-light)"></div>
  <div class="photo" role="img" aria-label="Man stretching on a foam roller on a blue mat" style="left:499px;top:2008px;width:470px;height:263px;background:linear-gradient(120deg,#efeeea,#d9d4cc 40%,#4e6fa3 70%,#2f59c4)"></div>
</section>

<section class="blog">
  <div class="abs blog-bg"></div>
  <div class="abs script" style="left:0;top:2440px;width:1200px">From The Blog</div>
  <div class="abs heading" style="left:0;top:2476px;width:1200px">LATEST BLOG</div>
  <div class="divider" style="top:2531px"><span></span></div>

  <article class="post" style="left:76px"><div class="photo" role="img" aria-label="Client resting beside a cryotherapy specialist" style="background:linear-gradient(135deg,#e9eef5,#3d7be0 45%,#1f2a3a)"></div><p>Lorem ipsum dolor sit dolore magna aliqua.</p><time>19 June 2019</time></article>
  <article class="post" style="left:345px"><div class="photo" role="img" aria-label="Two women talking during a consultation" style="background:linear-gradient(135deg,#ece7df,#c9b79f 50%,#8fb0c4)"></div><p>Lorem ipsum dolor sit dolore magna aliqua.</p><time>19 June 2019</time></article>
  <article class="post" style="left:614px"><div class="photo" role="img" aria-label="Woman in a misty cryotherapy chamber" style="background:linear-gradient(160deg,#efe4e2,#d6c8c6 40%,#7b9fb4 80%)"></div><p>Lorem ipsum dolor sit dolore magna aliqua.</p><time>19 June 2019</time></article>
  <article class="post" style="left:883px"><div class="photo" role="img" aria-label="Woman receiving a cryofacial with flowers nearby" style="background:linear-gradient(135deg,#f1efee,#e7d6cd 50%,#c7b6ad)"></div><p>Lorem ipsum dolor sit dolore magna aliqua.</p><time>19 June 2019</time></article>
</section>

<section class="pricing-section">
  <div class="photo" role="img" aria-label="Woman relaxing with eyes closed during a facial treatment" style="left:0;top:2988px;width:1200px;height:470px;background:linear-gradient(110deg,#c9b6a9,#d8b49a 30%,#c79a7a 55%,#e6e2df 90%)"></div>
  <div class="abs pricing">
    <h2>PRICING</h2>
    <div class="price-row" style="top:132px"><em>Whole Body Cryotherapy</em><b>$ 250.00</b></div>
    <div class="price-row" style="top:194px"><em>Localised Cryotherapy</em><b>$ 250.00</b></div>
    <div class="price-row last" style="top:257px"><em>Cryofacials</em><b>$ 250.00</b></div>
    <div class="outline-btn">GET IT</div>
  </div>
</section>

<section class="newsletter">
  <div class="abs script" style="left:0;top:3518px;width:1200px">Subscribe Now</div>
  <div class="abs heading" style="left:0;top:3554px;width:1200px">NEWSLETTER</div>
  <div class="divider" style="top:3609px"><span></span></div>
  <p>Lorem ipsum dolor sit amet, consectetur adipiscing elit, sed do tempor incididunt ut laboris nisi ut aliquip ex ea commodo consequat.</p>
  <div class="field" style="left:256px">
    <svg width="16" height="16" viewBox="0 0 16 16" fill="#b7c4d2"><circle cx="8" cy="5" r="4"/><path d="M0 16c0-5 4-7 8-7s8 2 8 7z"/></svg>Name :
  </div>
  <div class="field" style="left:491px">
    <svg width="18" height="13" viewBox="0 0 18 13" fill="none" stroke="#b7c4d2" stroke-width="1.6"><rect x="1" y="1" width="16" height="11"/><path d="M1 1l8 6 8-6"/></svg>Email :
  </div>
  <div class="btn" style="left:726px;top:3729px;width:218px;height:63px;font-weight:400;font-size:16px;text-transform:none">SUSCRIBE NOW</div>
</section>

<footer class="abs footer">
  <div class="logo">FROSTLINE<br>STUDIO</div>
  <div class="footer-menu">Home<span>|</span>About<span>|</span>Services<span>|</span>Online Booking<span>|</span>Pricing<span>|</span>Blog<span>|</span>Contact</div>
  <div class="social" aria-label="Social links"><i class="first"></i><i></i><i></i><i></i></div>
</footer>
<div class="abs copyright">Copyright ©&nbsp;<b>FROSTLINE STUDIO</b>&nbsp;- 2019 . All Right Reserved</div>

</body>
</html>
```